Business Card (double-sided) and Stationary Design for dental office

1) Business Card Design: We need a business card design for a dental specialty office.
Texts should contain:
The name of our office "Brindle Oaks Orthodontics"
Tagline: "Specialist in Orthodontic and Maxillofacial Orthopedics"
Tag line: "Creating "Tolvering" smiles for Children and Adults"
Doctor name: "Doctor Name"
Office Address:
"123 Street Name
City, State Zip code"
Office email address: office@brindleoaksortho.com
Website: www.brindleoaksortho.com

We will provide the full office address once the design is selected
Theme: beach, paradise, coastal, wave
We would like to have some creativity in design. Some acceptable ideas: front page: logo and office name. Back page: more detail information, and map to office in form of an island. Please see sample from our other location, but you DON'T HAVE TO USE OR COPY THE SAME CONCEPT.

IF POSSIBLE, PLEASE SUBMIT AT LEAST TWO CONCEPTS: ONE WITH THE BACK LOOKING SIMILAR TO WHAT IS IN THE SAMPLE, AND ONE DIFFERENT.

Color: designer to choose. We have different shade of blues and sand color in our office. Please see logo.

2) Please also design a matching set of stationary that compliment the business card and our logo.

Target Market(s)

Dental

Contact Information for Business Card

See descriptions

Font styles to use
Other font styles liked:
• Matching texts in logo

Colors
0054AA
0677BA
7BADD7
CADEEF
E8F1F8
0094D4
00A9DD
6FCCEA
C7EBF8
E9F6FB
00AB8E
00BBA5
67D7C9
C6EFE9
E9F9F6

Requirements
Must have
• Double-sided
Nice to have
• Beach coastal theme
Should not have
• Any shape or drawing of of tooth or teeth. We don’t need these. You don't necessarily have to just cut and paste the logo art and text as a whole, you have the liberty to rearrange the text.

```html
<!DOCTYPE html>
<html lang="en">
<head>
<meta charset="utf-8">
<title>Brindle Oaks Orthodontics – Business Card</title>
<link rel="stylesheet" href="https://fonts.googleapis.com/css2?family=Ubuntu:wght@500;700&family=Roboto:ital,wght@0,400;1,700&display=swap">
<style>
  :root {
    --backdrop: #8f8f8f;
    --card-light: #f1f1f1;
    --brand-teal: #3a8ea8;
    --brand-teal-dark: #2b7f99;
    --text-dark: #3b3b3b;
    --navy: #0d2f5a;
    --sky-top: #d3ebf6;
    --sky-bottom: #a9d8ef;
    --sea-mid: #00a9dd;
    --sea-deep: #0677ba;
    --sand: #e3b970;
    --white: #ffffff;
  }
  * { box-sizing: border-box; margin: 0; padding: 0; }
  html, body { width: 1200px; height: 410px; overflow: hidden; }
  body { background: var(--backdrop); position: relative; font-family: "Roboto", sans-serif; }

  .card {
    position: absolute;
    top: 42px;
    width: 552px;
    height: 316px;
    overflow: hidden;
    box-shadow: 0 3px 8px rgba(0,0,0,.35);
  }
  .card--front { left: 25px; background: var(--card-light); }
  .card--back  { left: 625px; }

  /* Front */
  .brand-mark { position: absolute; left: 237px; top: 2px; width: 310px; height: 310px; border-radius: 50%; background: var(--brand-teal); }
  .brand-name {
    position: absolute; left: 270px; top: 120px; width: 245px;
    font-family: "Ubuntu", sans-serif; font-weight: 700; font-size: 26px; line-height: 1.2;
    color: var(--white); text-align: center;
  }
  .person-name {
    position: absolute; left: 25px; top: 158px;
    font-family: "Ubuntu", sans-serif; font-weight: 700; font-size: 22px; letter-spacing: .5px;
    color: var(--brand-teal-dark);
  }
  .contact-list { position: absolute; left: 25px; top: 194px; list-style: none; font-size: 13px; color: var(--text-dark); line-height: 17px; }
  .contact-list li { display: flex; align-items: flex-start; gap: 8px; margin-bottom: 2px; }
  .contact-list svg { width: 11px; height: 11px; margin-top: 3px; flex: none; fill: var(--brand-teal-dark); }
  .contact-list .no-icon { padding-left: 19px; margin-top: -2px; }

  /* Back */
  .beach-scene {
    position: absolute; inset: 0;
    background:
      linear-gradient(160deg, transparent 55%, var(--sand) 85%),
      linear-gradient(180deg, var(--sky-top) 0%, var(--sky-bottom) 62%, var(--sea-mid) 78%, var(--sea-deep) 100%);
  }
  .office-block {
    position: absolute; left: 30px; top: 16px;
    font-style: normal; font-size: 14px; line-height: 18px; color: var(--text-dark);
  }
  .tagline {
    position: absolute; left: 6px; top: 261px; width: 280px; height: 20px;
    background: var(--white); border-radius: 0 10px 10px 0;
    font-style: italic; font-weight: 700; font-size: 11px; line-height: 20px;
    color: var(--navy); padding-left: 10px; white-space: nowrap;
  }
</style>
</head>
<body>

<section class="card card--front">
  <div class="brand-mark"></div>
  <p class="brand-name">Brindle Oaks Orthodontics</p>

  <h1 class="person-name">Daniel Harper</h1>
  <ul class="contact-list">
    <li><svg viewBox="0 0 10 10"><path d="M5 0a3.5 3.5 0 0 0-3.5 3.5C1.5 6 5 10 5 10s3.5-4 3.5-6.5A3.5 3.5 0 0 0 5 0zm0 5a1.4 1.4 0 1 1 0-2.8A1.4 1.4 0 0 1 5 5z"/></svg>123 Street Name</li>
    <li class="no-icon">City, State Zip code</li>
    <li><svg viewBox="0 0 10 10"><path d="M2 0.5l1.6 2.2-1 1.2a6 6 0 0 0 3.5 3.5l1.2-1L9.5 8 8.3 9.5C4 9.3 .7 6 .5 1.7z"/></svg>555-210-4836</li>
    <li><svg viewBox="0 0 10 10"><path d="M0 2h10v.8L5 5.8 0 2.8zM0 3.8l5 3 5-3V8H0z"/></svg>office@brindleoaksortho.com</li>
    <li><svg viewBox="0 0 10 10"><circle cx="5" cy="5" r="4.5"/></svg>brindleoaksortho.com</li>
  </ul>
</section>

<section class="card card--back">
  <div class="beach-scene" role="img" aria-label="Beach scene with sea waves, a sandy island with palm trees and a surfboard, and a map to the office"></div>
  <address class="office-block">
    Brindle Oaks Dentistry<br>
    123 Street Name<br>
    City, State Zip code
  </address>
  <p class="tagline">Specialist in Orthodontic &amp; Maxillofacial Orthopedics</p>
</section>

</body>
</html>
```